Cannabis & Shroom Informative

Online Blog/Informative website design
Example site: https://leafharborshop.com/

I will need the Ad space as well.

Target Market(s)

Cannabis and (psyho) Mushroom Users

Number of Pages Required

1 page

Colors

Designer to choose colors to be used in the design.

```html
<!DOCTYPE html>
<html lang="en">
<head>
<meta charset="utf-8">
<title>Greenfold Info – Cannabis &amp; Mushroom Informative</title>
<link rel="stylesheet" href="https://fonts.googleapis.com/css2?family=Roboto:wght@400;500;700&family=Raleway:wght@400;500&display=swap">
<style>
:root{
  --green:#3b8a1e;
  --green-bright:#4aa324;
  --ink:#1f1f1f;
  --text:#8a8a8a;
  --line:#e6e6e6;
  --dark:#231f20;
  --white:#ffffff;
}
*{box-sizing:border-box;margin:0;padding:0}
html,body{width:1200px;height:4198px;overflow:hidden;background:var(--white)}
body{position:relative;font-family:"Roboto",sans-serif;color:var(--ink)}
.abs{position:absolute}
p{font-family:"Raleway",sans-serif}

/* header */
.site-header{top:0;left:0;width:1200px;height:155px;background:var(--white)}
.brand{left:111px;top:14px;display:flex;flex-direction:column;align-items:flex-start;gap:10px}
.brand-dot{width:72px;height:72px;border-radius:50%;background:var(--green);margin-left:40px}
.brand-name{font-size:18px;font-weight:400;color:var(--ink);letter-spacing:.3px;white-space:nowrap}
.contact-bar{top:38px;left:582px;display:flex;align-items:center;gap:18px;font-size:14px;color:#888}
.contact-item{display:flex;align-items:center;gap:10px;font-family:"Raleway",sans-serif;white-space:nowrap}
.contact-item b{font-family:"Roboto",sans-serif;color:var(--ink);font-size:19px;font-weight:500}
.contact-icon{width:30px;height:30px;border:1px solid #ccc;border-radius:50%;display:flex;align-items:center;justify-content:center}
.main-nav{top:106px;left:455px;font-size:14px;font-weight:500}
.main-nav a{text-decoration:none;color:var(--ink);position:absolute;white-space:nowrap}
.main-nav a.active{color:var(--green-bright)}

/* hero */
.hero{top:155px;left:0;width:1200px;height:557px;background:linear-gradient(100deg,#5a534a 0%,#6d655a 40%,#5d564c 62%,#3f7a2a 80%,#5a9a33 100%)}
.hero-title{left:111px;top:348px;font-size:50px;font-weight:700;color:var(--white);letter-spacing:.5px;white-space:nowrap}
.hero-text{left:111px;top:411px;width:450px;font-size:14px;line-height:34px;color:#f1f1f1}
.btn-outline{left:111px;top:492px;width:158px;height:51px;border:2px solid var(--white);border-radius:3px;color:var(--white);font-size:14px;font-weight:500;display:flex;align-items:center;justify-content:center}
.dots{top:677px;left:561px;display:flex;gap:9px}
.dots span{width:9px;height:9px;border-radius:50%;background:var(--white)}

/* deal cards */
.deal-card{top:815px;width:318px;height:297px;border:1px solid var(--line);box-shadow:0 1px 4px rgba(0,0,0,.08);background:var(--white)}
.deal-img{position:absolute;left:5px;top:5px;width:306px;height:217px}
.deal-label{position:absolute;left:0;top:250px;width:100%;text-align:center;font-size:14px;font-weight:500}

.section-title{font-size:30px;font-weight:700;text-align:center;width:1200px;left:0}

/* products */
.product-img{height:409px;width:600px}
.product-card{width:488px;height:309px;background:var(--white);box-shadow:0 2px 10px rgba(0,0,0,.12);padding:46px 46px 0}
.product-card h3{font-size:25px;font-weight:500;margin-bottom:18px}
.product-card p{font-size:14px;line-height:33.5px;color:var(--text);text-align:justify;letter-spacing:.35px}
.arrow-btn{left:590px;top:1990px;width:54px;height:49px;background:var(--green);display:flex;align-items:center;justify-content:center}

/* ad band */
.ad-band{top:2194px;left:0;width:1200px;height:256px;background:var(--dark);overflow:hidden}
.ad-img{left:0;top:0;width:490px;height:256px}
.ad-headline{left:507px;top:2242px;font-size:23px;color:var(--green-bright);white-space:nowrap}
.ad-line{left:507px;font-size:24px;color:var(--white);white-space:nowrap}
.coupon{left:766px;top:2295px;width:127px;height:52px;background:var(--green);color:var(--white);font-size:24px;display:flex;align-items:center;justify-content:center}

/* blog */
.blog-card{width:318px;height:430px;border:1px solid var(--line);box-shadow:0 1px 4px rgba(0,0,0,.08);background:var(--white)}
.blog-img{position:absolute;left:5px;top:5px;width:306px;height:207px}
.blog-date{position:absolute;left:5px;top:174px;width:196px;height:38px;background:var(--green);color:var(--white);font-family:"Raleway",sans-serif;font-size:17px;display:flex;align-items:center;gap:14px;padding-left:28px}
.blog-body{position:absolute;left:27px;top:240px;width:270px}
.blog-body h4{font-size:14px;font-weight:500;margin-bottom:14px}
.blog-body p{font-size:14px;line-height:29px;color:var(--text)}
.blog-meta{display:flex;align-items:center;margin-top:12px;font-size:14px;color:#777}
.blog-meta a{color:var(--green);font-family:"Roboto",sans-serif;font-weight:500;text-decoration:underline;margin-right:auto}
.meta-item{display:flex;align-items:center;gap:5px;margin-left:12px;font-family:"Raleway",sans-serif}

/* about */
.about-title{left:111px;top:3590px;font-size:30px;font-weight:700}
.about-text{left:111px;top:3646px;width:482px;font-size:14px;line-height:34px;color:var(--text);text-align:justify}
.btn-solid{left:111px;top:3941px;width:155px;height:51px;background:var(--green);color:var(--white);font-size:16px;font-weight:500;display:flex;align-items:center;justify-content:center}
.about-img{left:631px;top:3619px;width:440px;height:352px}

.site-footer{left:0;top:4096px;width:1200px;height:102px;background:var(--dark);color:#eee;font-family:"Raleway",sans-serif;font-size:15px;display:flex;align-items:center;justify-content:center}
</style>
</head>
<body>

<header class="site-header abs">
  <div class="brand abs"><span class="brand-dot"></span><span class="brand-name">GREENFOLD INFO</span></div>
  <div class="contact-bar abs">
    <div class="contact-item">
      <span class="contact-icon"><svg width="14" height="14" viewBox="0 0 24 24"><path d="M6.6 10.8a15 15 0 0 0 6.6 6.6l2.2-2.2a1 1 0 0 1 1-.25 11 11 0 0 0 3.6.6 1 1 0 0 1 1 1V20a1 1 0 0 1-1 1A17 17 0 0 1 3 4a1 1 0 0 1 1-1h3.5a1 1 0 0 1 1 1 11 11 0 0 0 .6 3.6 1 1 0 0 1-.25 1z" fill="#4aa324"/></svg></span>
      <span>Call Now - <b>555-214-7730</b></span>
    </div>
    <div class="contact-item">
      <span class="contact-icon"><svg width="14" height="14" viewBox="0 0 24 24"><rect x="3" y="5" width="18" height="14" rx="1" fill="none" stroke="#4aa324" stroke-width="2"/><path d="M3 6l9 7 9-7" fill="none" stroke="#4aa324" stroke-width="2"/></svg></span>
      <span>sales@greenfoldinfo.com</span>
    </div>
  </div>
  <nav class="main-nav abs">
    <a class="active" style="left:0">HOME</a>
    <a style="left:98px">ABOUT</a>
    <a style="left:202px">REVIEWS</a>
    <a style="left:324px">PRODUCTS</a>
    <a style="left:463px">NEWS</a>
    <a style="left:560px">CONTACT</a>
  </nav>
</header>

<section class="hero abs" role="img" aria-label="Cannabis leaves lying on weathered wooden planks"></section>
<h1 class="hero-title abs">GREENFOLD INFO</h1>
<p class="hero-text abs">Nemo enim ipsam voluptatem quia voluptas sit aspernatur aut odit aut fugit, sed quia consequuntur</p>
<div class="btn-outline abs">GET STARTED</div>
<div class="dots abs"><span></span><span></span><span></span><span></span><span></span></div>

<article class="deal-card abs" style="left:111px">
  <div class="deal-img" role="img" aria-label="Young cannabis seedling in soil at sunset" style="background:linear-gradient(160deg,#f0b23a,#9a6a1f 55%,#3b2a14)"></div>
  <div class="deal-label">CANNABIS DEALS</div>
</article>
<article class="deal-card abs" style="left:440px">
  <div class="deal-img" role="img" aria-label="Bowl of fresh mushrooms on a dark table" style="background:radial-gradient(circle at 60% 50%,#b88d66,#6b5848 45%,#3c3a38)"></div>
  <div class="deal-label">MUSHROOM DEALS</div>
</article>
<article class="deal-card abs" style="left:771px">
  <div class="deal-img" role="img" aria-label="Two hands exchanging a red gift card" style="background:linear-gradient(180deg,#c7d0dc,#e9ecf2 60%,#d8b8a8)"></div>
  <div class="deal-label">OFFER COUPON CODES</div>
</article>

<h2 class="section-title abs" style="top:1210px">OUR PRODUCTS</h2>

<div class="product-img abs" style="left:0;top:1273px;background:linear-gradient(180deg,#efeeea 0%,#d9d3c2 45%,#7d8a4a 70%,#8a6a48 100%)" role="img" aria-label="Cannabis buds beside oil bottles on a wooden board"></div>
<div class="product-card abs" style="left:559px;top:1322px">
  <h3>CANNABIS</h3>
  <p>Nemo enim ipsam voluptatem quia voluptas sit aspernatur aut odit aut fugit, sed quia consequuntur magni dolores eos qui ratione voluptatem sequi nesciunt. Neque porro quisquam est, qui dolorem ipsum quia dolor sit amet, consectetur,</p>
</div>

<div class="product-img abs" style="left:600px;top:1682px;background:radial-gradient(circle at 50% 50%,#a07a58,#3d3632 45%,#2c2622)" role="img" aria-label="Pan of mushrooms on a dark wooden table"></div>
<div class="product-card abs" style="left:155px;top:1729px">
  <h3>MUSHROOM</h3>
  <p>Nemo enim ipsam voluptatem quia voluptas sit aspernatur aut odit aut fugit, sed quia consequuntur magni dolores eos qui ratione voluptatem sequi nesciunt. Neque porro quisquam est, qui dolorem ipsum quia dolor sit amet, consectetur,</p>
</div>
<div class="arrow-btn abs"><svg width="22" height="16" viewBox="0 0 22 16"><path d="M1 8h19M13 1l7 7-7 7" fill="none" stroke="#fff" stroke-width="2"/></svg></div>

<section class="ad-band abs">
  <div class="ad-img abs" role="img" aria-label="Dried mushrooms and cannabis buds on a wooden board" style="background:linear-gradient(90deg,#7a6650,#a18a6c 60%,#8a7256);border-radius:0 50% 50% 0/0 100% 100% 0"></div>
</section>
<div class="ad-headline abs">BUY WEED TODAY WITH CANNABIS WHOLESALERS</div>
<div class="ad-line abs" style="top:2306px">USE OUR CUPPON -</div>
<div class="coupon abs">XAD657</div>
<div class="ad-line abs" style="top:2372px">FREE SHIPPING ON ORDER $100</div>

<h2 class="section-title abs" style="top:2548px;left:-6px">LATEST BLOG</h2>

<article class="blog-card abs" style="left:111px;top:2610px">
  <div class="blog-img" role="img" aria-label="Cannabis leaf with THC and CBD molecule graphics" style="background:linear-gradient(135deg,#6e6a60,#4e6a3a 60%,#3a3a32)"></div>
  <div class="blog-date"><svg width="16" height="16" viewBox="0 0 16 16"><rect x="1" y="2" width="14" height="13" fill="none" stroke="#cfe6c2" stroke-width="1.5"/><path d="M1 6h14" stroke="#cfe6c2" stroke-width="1.5"/></svg>10-01-2020</div>
  <div class="blog-body"><h4>LOREM IPSUM DOLOR SIT AMET</h4><p>Nemo enim ipsam voluptatem quia voluptas sit aspernatur aut odit aut fugit, sed quia consequuntur</p>
  <div class="blog-meta"><a>READ MORE</a><span class="meta-item">♡ 15</span><span class="meta-item">▤ 15</span><span class="meta-item">➦ 15</span></div></div>
</article>
<article class="blog-card abs" style="left:441px;top:2610px">
  <div class="blog-img" role="img" aria-label="Basket of white mushrooms" style="background:linear-gradient(135deg,#8a6a4a,#d6c6aa 50%,#5a4a32)"></div>
  <div class="blog-date"><svg width="16" height="16" viewBox="0 0 16 16"><rect x="1" y="2" width="14" height="13" fill="none" stroke="#cfe6c2" stroke-width="1.5"/><path d="M1 6h14" stroke="#cfe6c2" stroke-width="1.5"/></svg>10-01-2020</div>
  <div class="blog-body"><h4>LOREM IPSUM DOLOR SIT AMET</h4><p>Nemo enim ipsam voluptatem quia voluptas sit aspernatur aut odit aut fugit, sed quia consequuntur</p>
  <div class="blog-meta"><a>READ MORE</a><span class="meta-item">♡ 15</span><span class="meta-item">▤ 15</span><span class="meta-item">➦ 15</span></div></div>
</article>
<article class="blog-card abs" style="left:771px;top:2610px">
  <div class="blog-img" role="img" aria-label="Medical cannabis jar spilling buds onto a table" style="background:linear-gradient(135deg,#8aa0c0,#e4e8ee 50%,#8a6a4a)"></div>
  <div class="blog-date"><svg width="16" height="16" viewBox="0 0 16 16"><rect x="1" y="2" width="14" height="13" fill="none" stroke="#cfe6c2" stroke-width="1.5"/><path d="M1 6h14" stroke="#cfe6c2" stroke-width="1.5"/></svg>10-01-2020</div>
  <div class="blog-body"><h4>LOREM IPSUM DOLOR SIT AMET</h4><p>Nemo enim ipsam voluptatem quia voluptas sit aspernatur aut odit aut fugit, sed quia consequuntur</p>
  <div class="blog-meta"><a>READ MORE</a><span class="meta-item">♡ 15</span><span class="meta-item">▤ 15</span><span class="meta-item">➦ 15</span></div></div>
</article>
<article class="blog-card abs" style="left:111px;top:3064px">
  <div class="blog-img" role="img" aria-label="Wild mushrooms on a wooden board with herbs" style="background:linear-gradient(135deg,#4a3a2a,#a07840 50%,#3a4a2a)"></div>
  <div class="blog-date"><svg width="16" height="16" viewBox="0 0 16 16"><rect x="1" y="2" width="14" height="13" fill="none" stroke="#cfe6c2" stroke-width="1.5"/><path d="M1 6h14" stroke="#cfe6c2" stroke-width="1.5"/></svg>10-01-2020</div>
  <div class="blog-body"><h4>LOREM IPSUM DOLOR SIT AMET</h4><p>Nemo enim ipsam voluptatem quia voluptas sit aspernatur aut odit aut fugit, sed quia consequuntur</p>
  <div class="blog-meta"><a>READ MORE</a><span class="meta-item">♡ 15</span><span class="meta-item">▤ 15</span><span class="meta-item">➦ 15</span></div></div>
</article>
<article class="blog-card abs" style="left:441px;top:3064px">
  <div class="blog-img" role="img" aria-label="Indoor cannabis grow room with rows of plants" style="background:linear-gradient(180deg,#e8ebe6,#c8cfc6 40%,#4a7a32 70%,#3a5a2a)"></div>
  <div class="blog-date"><svg width="16" height="16" viewBox="0 0 16 16"><rect x="1" y="2" width="14" height="13" fill="none" stroke="#cfe6c2" stroke-width="1.5"/><path d="M1 6h14" stroke="#cfe6c2" stroke-width="1.5"/></svg>10-01-2020</div>
  <div class="blog-body"><h4>LOREM IPSUM DOLOR SIT AMET</h4><p>Nemo enim ipsam voluptatem quia voluptas sit aspernatur aut odit aut fugit, sed quia consequuntur</p>
  <div class="blog-meta"><a>READ MORE</a><span class="meta-item">♡ 15</span><span class="meta-item">▤ 15</span><span class="meta-item">➦ 15</span></div></div>
</article>
<article class="blog-card abs" style="left:771px;top:3064px">
  <div class="blog-img" role="img" aria-label="Hands placing forest mushrooms into a wicker basket" style="background:linear-gradient(135deg,#5a4a3a,#9a7048 50%,#3a3a2a)"></div>
  <div class="blog-date"><svg width="16" height="16" viewBox="0 0 16 16"><rect x="1" y="2" width="14" height="13" fill="none" stroke="#cfe6c2" stroke-width="1.5"/><path d="M1 6h14" stroke="#cfe6c2" stroke-width="1.5"/></svg>10-01-2020</div>
  <div class="blog-body"><h4>LOREM IPSUM DOLOR SIT AMET</h4><p>Nemo enim ipsam voluptatem quia voluptas sit aspernatur aut odit aut fugit, sed quia consequuntur</p>
  <div class="blog-meta"><a>READ MORE</a><span class="meta-item">♡ 15</span><span class="meta-item">▤ 15</span><span class="meta-item">➦ 15</span></div></div>
</article>

<h2 class="about-title abs">ABOUT US</h2>
<p class="about-text abs">Nemo enim ipsam voluptatem quia voluptas sit aspernatur aut odit aut fugit, sed quia consequuntur magni dolores eos qui ratione voluptatem sequi nesciunt. Neque porro quisquam est, qui dolorem ipsum quia dolor sit amet, consectetur, adipisci velit, sed quia non numquam eius modi tempora incidunt ut labore et dolore magnam aliquam quaerat voluptatem.Neque porro quisquam est, qui dolorem ipsum quia dolor sit amet, consectetur, adipisci velit,</p>
<div class="btn-solid abs">READ MORE</div>
<div class="about-img abs" role="img" aria-label="Hands cradling a young cannabis plant" style="background:radial-gradient(circle at 50% 55%,#6a8a3a,#a89a5a 50%,#4a4a2a)"></div>

<footer class="site-footer abs">© 2020 All Rights Reserved</footer>

</body>
</html>
```